Varentoria Business Card and Letter Head

We are a leadership assessment consultancy based in Sydney, Australia. We help executive-level decison-makers select leaders for more senior level roles in corporate and government organisations. Our methodology is based on the latest research from the field of neuroscience.
We need a business card design and matching letter head that presents our company, Varentoria, as a:
1. trusted adviser to senior executive-level decison makers
2. niche consultancy who are experts in the field of assessing leadership talent
3. results-focused solution provider who balance scientific methods with pragmatic solutions
The following company details should be used in all designs:
Company Name: Varentoria
Details (for business card):
Derek Hanford
Prime Capacity Officer
Level 29, Marlow Tower
7 Marlow Square
Sydney, NSW 2000 Australia
Phone: 1300 582 714
Mobile: 0412 637 258
Email: derek.hanford@varentoria-example.com.au
Website: varentoria-example.com.au
I have attached the logo for Varentoria (for both a white and black background) - your business card and letter head designs must incoporate this logo and colour scheme.
Thanks for your interest in this project, I'm looking forward to receiving your ideas.
Regards,
Derek
Target Market(s)
Executive-level decison-makers in corporate and government organisations (e.g., CEO, VP, Head of Human Resources)
Industry/Entity Type
Leadership
Look and feel

```html
<!DOCTYPE html>
<html lang="en">
<head>
<meta charset="utf-8">
<title>Varentoria Business Card</title>
<link rel="stylesheet" href="https://fonts.googleapis.com/css2?family=Open+Sans:wght@300;400;600;700&display=swap">
<style>
  :root {
    --backdrop: #5e3d26;
    --card: #ffffff;
    --ink: #3b3b3e;
    --accent: #b42a1f;
    --muted: #4a4a4d;
  }
  * { margin: 0; padding: 0; box-sizing: border-box; }
  html, body {
    width: 1200px; height: 427px; overflow: hidden;
    background: var(--backdrop);
    font-family: "Open Sans", Arial, sans-serif;
  }
  .canvas { position: relative; width: 1200px; height: 427px; }

  .card {
    position: absolute;
    width: 518px; height: 295px;
    background: var(--card);
    border-radius: 20px;
    box-shadow: 0 4px 14px rgba(0,0,0,0.35);
  }
  .card--front { left: 62px; top: 68px; }
  .card--back  { left: 610px; top: 67px; }

  /* front */
  .brand {
    position: absolute; left: 63px; top: 30px;
    display: flex; align-items: center; gap: 18px;
  }
  .brand__square { width: 84px; height: 84px; background: var(--ink); }
  .brand__text { display: flex; flex-direction: column; }
  .brand__name {
    font-weight: 700; font-size: 50px; line-height: 1;
    color: var(--ink); letter-spacing: -1px;
  }
  .brand__tagline {
    margin-top: 10px;
    font-weight: 300; font-size: 15.5px; letter-spacing: 0.6px;
    color: var(--muted); text-transform: uppercase;
  }
  .person { position: absolute; left: 0; right: 0; top: 156px; text-align: center; }
  .person__name {
    font-size: 19px; font-weight: 400; color: var(--accent);
    text-transform: uppercase; line-height: 1.2;
  }
  .person__title { font-size: 12px; color: var(--ink); margin-top: 2px; }

  .contact {
    position: absolute; left: 0; right: 0; top: 219px;
    text-align: center; font-size: 12.3px; color: var(--ink); line-height: 21px;
  }
  .contact__label { color: var(--accent); }
  .contact__item { margin: 0 6px; }
  .website {
    position: absolute; left: 0; right: 0; top: 268px;
    text-align: center; font-size: 11.5px; font-weight: 700;
    letter-spacing: 1px; color: var(--ink);
  }

  /* back */
  .mark {
    position: absolute; left: 0; right: 0; top: 92px;
    display: flex; justify-content: center; align-items: center; gap: 14px;
  }
  .mark__square { width: 40px; height: 40px; background: var(--accent); }
  .mark__name { font-weight: 700; font-size: 46px; color: var(--ink); letter-spacing: -1px; }
  .back-url {
    position: absolute; left: 0; right: 0; top: 229px;
    text-align: center; font-size: 13px; letter-spacing: 1.6px;
    color: var(--ink); text-transform: uppercase;
  }
</style>
</head>
<body>
<main class="canvas">
  <section class="card card--front">
    <div class="brand">
      <div class="brand__square"></div>
      <div class="brand__text">
        <span class="brand__name">Varentoria</span>
        <span class="brand__tagline">Assessing Tomorrow's Leaders</span>
      </div>
    </div>
    <div class="person">
      <p class="person__name">Derek Hanford</p>
      <p class="person__title">Prime Capacity Officer</p>
    </div>
    <div class="contact">
      <p>Level 29, Marlow Tower, 7 Marlow Square Sydney, NSW 2000 Australia</p>
      <p>
        <span class="contact__item"><span class="contact__label">P:</span> 1300 582 714</span>
        <span class="contact__item"><span class="contact__label">M:</span> 0412 637 258</span>
        <span class="contact__item"><span class="contact__label">E:</span> derek.hanford@varentoria-example.com.au</span>
      </p>
    </div>
    <p class="website">www.varentoria-example.com.au</p>
  </section>

  <section class="card card--back">
    <div class="mark">
      <div class="mark__square"></div>
      <span class="mark__name">Varentoria</span>
    </div>
    <p class="back-url">varentoria-example.com.au</p>
  </section>
</main>
</body>
</html>
```